Business Card Design needed - Something Awesome!

Need a business card designed. Company is "Marlowe Advisory" we do consulting and also have sales automation technology.
I'm going to use thick stock or metal, something really nice... I was thinking about a QR Code on the back that would just upload my contact info to the persons contact, etc -

This is a Strategy Company with a tech feel. I'm open to ideas but really want this to be nice!

I need a template that should include:

Name | Position or Title
D: 415.902.3376
www.marloweadvisory.example

I'm going to attach my contact so you can use that one, I need to get this printed.

Target Market(s)

Small to mid size customers, Entrepreneurs etc.

Industry/Entity Type

Consulting, Tech, Private Equity.

Contact Information for Business Card

Name, Phone, Maybe email, URL

Font styles to use
Sans Serif

Colors

Designer to choose only greyscale colors for use in the design.

Requirements
Must have
• Fresh, Clean, stand out from the crowd - will be on thick stock or metal.
Nice to have
• Clean, simple yet impactful.
Should not have
• Not cartoonish

```html
<!DOCTYPE html>
<html lang="en">
<head>
<meta charset="utf-8">
<title>Marlowe Advisory — Business Card</title>
<link rel="stylesheet" href="https://fonts.googleapis.com/css2?family=Roboto:wght@400;500;700&display=swap">
<style>
  :root {
    --backdrop: #2f2f2f;
    --card: #121212;
    --card-edge: #1c1c1c;
    --silver: #c9c9c9;
    --silver-soft: #9a9a9a;
    --rule: #7a7a7a;
    --pattern-dark: #0b0b0b;
    --pattern-mid: #262626;
    --pattern-light: #3a3a3a;
  }
  * { margin: 0; padding: 0; box-sizing: border-box; }
  html, body { width: 1200px; height: 801px; overflow: hidden; }
  body {
    background: var(--backdrop);
    font-family: "Roboto", Arial, sans-serif;
    position: relative;
  }
  .card {
    position: absolute;
    top: 252px;
    width: 520px;
    height: 297px;
    background: var(--card);
    border: 1px solid var(--card-edge);
    box-shadow: 0 10px 28px rgba(0,0,0,0.45);
    overflow: hidden;
  }
  .card-front { left: 50px; }
  .card-back { left: 630px; }

  .brand-name {
    position: absolute;
    left: 34px;
    top: 40px;
    font-size: 27px;
    font-weight: 500;
    letter-spacing: 3px;
    color: var(--silver);
    text-transform: uppercase;
    line-height: 1.15;
  }
  .person {
    position: absolute;
    right: 34px;
    top: 44px;
    text-align: right;
  }
  .person-name {
    font-size: 15px;
    font-weight: 700;
    letter-spacing: 1.5px;
    color: var(--silver-soft);
    text-transform: uppercase;
  }
  .person-title {
    margin-top: 4px;
    font-size: 12px;
    color: var(--silver-soft);
  }
  .rule {
    position: absolute;
    height: 1px;
    background: var(--rule);
  }
  .rule-top { right: 34px; top: 96px; width: 270px; }
  .rule-bottom { left: 34px; top: 196px; width: 270px; }

  .contact-list {
    position: absolute;
    left: 34px;
    top: 208px;
    list-style: none;
  }
  .contact-item {
    display: flex;
    align-items: center;
    gap: 7px;
    font-size: 12.5px;
    color: var(--silver-soft);
    line-height: 19px;
  }
  .contact-icon { width: 10px; height: 10px; flex: none; }

  .back-pattern {
    position: absolute;
    inset: 0;
    background: linear-gradient(120deg, var(--pattern-dark) 0%, var(--pattern-mid) 55%, var(--pattern-light) 100%);
  }
  .back-brand {
    position: absolute;
    left: 0; right: 0;
    top: 50%;
    transform: translateY(-50%);
    text-align: center;
    display: flex;
    align-items: center;
    justify-content: center;
    gap: 12px;
    font-size: 20px;
    font-weight: 500;
    letter-spacing: 3px;
    color: var(--silver);
    text-transform: uppercase;
  }
  .back-brand-square {
    width: 14px; height: 14px;
    background: var(--silver);
  }
</style>
</head>
<body>
  <section class="card card-front" aria-label="Business card front">
    <div class="brand-name">Marlowe<br>Advisory</div>
    <div class="person">
      <div class="person-name">Julian R. Hale</div>
      <div class="person-title">Founder / CEO</div>
    </div>
    <div class="rule rule-top"></div>
    <div class="rule rule-bottom"></div>
    <ul class="contact-list">
      <li class="contact-item">
        <svg class="contact-icon" viewBox="0 0 10 10" aria-hidden="true">
          <circle cx="5" cy="5" r="5" fill="#9a9a9a"/>
          <path d="M3.2 2.6l1 1-.5.6c.3.6.8 1.1 1.4 1.4l.6-.5 1 1-.6.8C4.6 6.7 3.3 5.4 2.4 3.2z" fill="#121212"/>
        </svg>
        415.902.3376
      </li>
      <li class="contact-item">
        <svg class="contact-icon" viewBox="0 0 10 10" aria-hidden="true">
          <circle cx="5" cy="5" r="5" fill="#9a9a9a"/>
          <rect x="2.4" y="3.2" width="5.2" height="3.6" fill="#121212"/>
          <path d="M2.4 3.2L5 5.2l2.6-2" stroke="#9a9a9a" stroke-width=".6" fill="none"/>
        </svg>
        info@marloweadvisory.example
      </li>
      <li class="contact-item">
        <svg class="contact-icon" viewBox="0 0 10 10" aria-hidden="true">
          <circle cx="5" cy="5" r="5" fill="#9a9a9a"/>
          <circle cx="5" cy="5" r="2.8" fill="none" stroke="#121212" stroke-width=".7"/>
          <path d="M2.2 5h5.6M5 2.2v5.6" stroke="#121212" stroke-width=".6"/>
        </svg>
        www.marloweadvisory.example
      </li>
    </ul>
  </section>

  <section class="card card-back" aria-label="Business card back">
    <div class="back-pattern" role="img" aria-label="Tonal pattern of glossy black squares on matte black"></div>
    <div class="back-brand"><span class="back-brand-square"></span>Marlowe Advisory</div>
  </section>
</body>
</html>
```